Need Business Card ASAP

We need a business card design for a meeting coming up in a few days. The company name is Harlow Ridge Building and Construction and the logo is attached. Something clean, cool, and contemporary that we can get to a printer right away. Attached is the business card for Volmar Energy, an affiliated company, which we like. Instead of the hawk on the back, you could use the attached "D". We'll also be needing matching letterhead in the near future, so ideas for that are welcome.

```html
<!DOCTYPE html>
<html lang="en">
<head>
<meta charset="utf-8">
<title>Harlow Ridge Building and Construction – Business Card</title>
<link rel="stylesheet" href="https://fonts.googleapis.com/css2?family=Arimo:wght@400;700&display=swap">
<style>
  :root {
    --page: #efece4;
    --paper: #ffffff;
    --khaki: #b3ab7c;
    --khaki-light: #e2dec9;
    --khaki-mid: #c7bf9b;
    --ink: #231f20;
    --ink-soft: #2e2b2a;
  }
  * { margin: 0; padding: 0; box-sizing: border-box; }
  html, body {
    width: 1034px; height: 1200px; overflow: hidden;
    background: var(--page);
    font-family: "Arimo", Arial, sans-serif;
    color: var(--ink);
  }
  .card {
    position: absolute; left: 72px; width: 889px; height: 507px;
    overflow: hidden;
    box-shadow: 0 2px 6px rgba(0,0,0,.18);
  }
  .card--front { top: 59px; background: var(--paper); }
  .card--back {
    top: 600px;
    background: linear-gradient(180deg, var(--khaki-mid) 0%, var(--khaki-light) 100%);
    display: flex; align-items: center; justify-content: center;
  }
  .wave { position: absolute; inset: 0; width: 100%; height: 100%; }

  .brand-block {
    position: absolute; left: 42px; top: 39px; width: 237px; height: 299px;
    background: linear-gradient(160deg, #d9d3b6 0%, var(--khaki) 100%);
    display: flex; align-items: flex-end; padding: 0 18px 26px;
  }
  .brand-block__name {
    font-size: 25px; line-height: 1.2; font-weight: 700; color: var(--ink);
  }

  .company {
    position: absolute; left: 343px; top: 40px;
    font-size: 27px; line-height: 1.22; font-weight: 400;
    color: var(--khaki); text-transform: uppercase; letter-spacing: .2px;
  }
  .company__address {
    position: absolute; left: 343px; top: 117px;
    font-size: 21px; color: var(--ink);
  }

  .contact {
    position: absolute; right: 27px; top: 272px; text-align: right;
  }
  .contact__name { font-size: 30px; font-weight: 700; line-height: 33px; }
  .contact__title { font-size: 21px; font-weight: 700; line-height: 24px; margin-top: 2px; margin-bottom: 10px; }
  .contact__line {
    display: flex; justify-content: flex-end; align-items: center; gap: 8px;
    font-size: 23px; line-height: 39px;
  }
  .contact__icon { width: 18px; height: 18px; fill: var(--ink-soft); }

  .back__name {
    font-size: 46px; font-weight: 700; color: var(--ink);
    text-align: center; line-height: 1.2;
  }
</style>
</head>
<body>

<section class="card card--front" aria-label="Business card front">
  <svg class="wave" viewBox="0 0 526 300" preserveAspectRatio="none" aria-hidden="true">
    <defs>
      <linearGradient id="khakiFill" x1="0" y1="0" x2="0" y2="1">
        <stop offset="0" stop-color="#c2ba94"/>
        <stop offset="1" stop-color="#e4e0cc"/>
      </linearGradient>
      <clipPath id="leftAccent"><rect x="0" y="0" width="210" height="300"/></clipPath>
      <clipPath id="rightAccent"><rect x="370" y="0" width="156" height="300"/></clipPath>
    </defs>
    <path d="M0 268 C170 266 260 134 526 142 L526 300 L0 300 Z" fill="url(#khakiFill)"/>
    <path d="M0 258 C170 256 260 124 526 132 L526 142 C260 134 170 266 0 268 Z" fill="#231f20"/>
    <path d="M0 240 C170 238 260 106 526 114 L526 124 C260 116 170 248 0 250 Z" fill="#b3ab7c" clip-path="url(#leftAccent)"/>
    <path d="M0 240 C170 238 260 106 526 114 L526 124 C260 116 170 248 0 250 Z" fill="#b3ab7c" clip-path="url(#rightAccent)"/>
  </svg>

  <div class="brand-block">
    <span class="brand-block__name">Harlow Ridge Building and Construction</span>
  </div>

  <h1 class="company">Harlow Ridge Building<br>&amp; Construction</h1>
  <p class="company__address">00, Complex Name, Street, City 00000</p>

  <div class="contact">
    <p class="contact__name">Your Name</p>
    <p class="contact__title">Title</p>
    <p class="contact__line">
      <svg class="contact__icon" viewBox="0 0 24 24" aria-hidden="true"><path d="M6.6 10.8a15.1 15.1 0 0 0 6.6 6.6l2.2-2.2c.3-.3.7-.4 1-.2 1.1.4 2.3.6 3.6.6.6 0 1 .4 1 1V20c0 .6-.4 1-1 1A17 17 0 0 1 3 4c0-.6.4-1 1-1h3.5c.6 0 1 .4 1 1 0 1.3.2 2.5.6 3.6.1.3 0 .7-.2 1z"/></svg>
      (123) 456-7890
    </p>
    <p class="contact__line">
      <svg class="contact__icon" viewBox="0 0 24 24" aria-hidden="true"><path d="M8 1h8a2 2 0 0 1 2 2v18a2 2 0 0 1-2 2H8a2 2 0 0 1-2-2V3a2 2 0 0 1 2-2zm0 3v13h8V4zm4 15a1 1 0 1 0 0 2 1 1 0 0 0 0-2z"/></svg>
      (123) 456-7890
    </p>
    <p class="contact__line">
      <svg class="contact__icon" viewBox="0 0 24 24" aria-hidden="true"><path d="M2 6h20v12H2zm2 2v.3l8 5 8-5V8l-8 5z"/></svg>
      yourname@harlowridgebuilding.com
    </p>
    <p class="contact__line">
      <svg class="contact__icon" viewBox="0 0 24 24" aria-hidden="true"><path d="M12 2a10 10 0 1 0 0 20 10 10 0 0 0 0-20zm6.9 9h-3a15 15 0 0 0-1.3-5.5A8 8 0 0 1 18.9 11zM12 4c.9 1.2 1.8 3.6 2 7h-4c.2-3.4 1.1-5.8 2-7zM9.4 5.5A15 15 0 0 0 8.1 11h-3a8 8 0 0 1 4.3-5.5zM5.1 13h3a15 15 0 0 0 1.3 5.5A8 8 0 0 1 5.1 13zM12 20c-.9-1.2-1.800-3.6-2-7h4c-.2 3.4-1.1 5.8-2 7zm2.6-1.5a15 15 0 0 0 1.3-5.5h3a8 8 0 0 1-4.3 5.5z"/></svg>
      www.harlowridgebuilding.com
    </p>
  </div>
</section>

<section class="card card--back" aria-label="Business card back">
  <p class="back__name">Harlow Ridge<br>Building and Construction</p>
</section>

</body>
</html>
```